Real Estate investment company needs billboard designs

This is our website: https://brightlanepropertygroup.com/
We are looking for some billboard concepts that uses our CEO in the design. I have attached some images and 1 billboard design that someone in our industry uses, but we don't want it exactly like his.

Industry/Entity Type

real estate

Colors

Designer to choose colors to be used in the design.

Requirements
Must have
• Company colors from websiute

```html
<!DOCTYPE html>
<html lang="en">
<head>
<meta charset="UTF-8">
<title>Bright Lane Property Group – Billboard</title>
<link rel="stylesheet" href="https://fonts.googleapis.com/css2?family=Poppins:wght@400;500;700;800&family=Roboto:wght@900&display=swap">
<style>
  :root {
    --stage: #8a8a8a;
    --paper: #ffffff;
    --brand-red: #d90f16;
    --ink-navy: #161a3a;
    --photo-light: #c9d7e8;
    --photo-mid: #8fa8c8;
  }
  * { margin: 0; padding: 0; box-sizing: border-box; }
  html, body { width: 971px; height: 1200px; overflow: hidden; }
  body { background: var(--stage); position: relative; font-family: "Poppins", sans-serif; }

  .billboard {
    position: absolute; left: 36px; top: 376px;
    width: 900px; height: 449px;
    background: var(--paper);
    overflow: hidden;
    box-shadow: 0 10px 28px rgba(0,0,0,.35);
  }
  .roof-band { position: absolute; inset: 0; width: 900px; height: 449px; }
  .bottom-rule {
    position: absolute; left: 0; top: 437px; width: 636px; height: 12px;
    background: var(--brand-red);
  }
  .ceo-photo {
    position: absolute; left: 636px; top: 8px; width: 264px; height: 441px;
    border-radius: 110px 110px 0 0;
    background: linear-gradient(180deg, var(--photo-light), var(--photo-mid));
  }
  .headline {
    position: absolute; left: 43px; top: 36px;
    font-size: 56px; font-weight: 800; line-height: 1;
    color: var(--ink-navy); letter-spacing: -0.5px; white-space: nowrap;
  }
  .offer-kicker {
    position: absolute; left: 44px; top: 155px;
    font-size: 38px; font-weight: 700; line-height: 1;
    color: var(--paper); white-space: nowrap; letter-spacing: -0.3px;
  }
  .offer-main {
    position: absolute; left: 42px; top: 199px;
    font-size: 71px; font-weight: 500; line-height: 1;
    color: var(--paper); white-space: nowrap;
  }
  .phone {
    position: absolute; left: 43px; top: 324px;
    font-family: "Roboto", sans-serif; font-weight: 900;
    font-size: 43px; line-height: 1; letter-spacing: -1px;
    color: var(--ink-navy); white-space: nowrap;
  }
  .divider {
    position: absolute; left: 338px; top: 318px; width: 1px; height: 48px;
    background: var(--ink-navy);
  }
  .company-name {
    position: absolute; left: 354px; top: 326px;
    font-size: 13px; font-weight: 700; line-height: 1.35;
    color: var(--ink-navy); white-space: nowrap;
  }
  .website {
    position: absolute; left: 43px; top: 371px;
    font-size: 30px; font-weight: 400; line-height: 1;
    color: var(--ink-navy); white-space: nowrap;
  }
</style>
</head>
<body>
  <section class="billboard">
    <svg class="roof-band" viewBox="0 0 1420 708" preserveAspectRatio="none" aria-hidden="true">
      <polygon fill="var(--brand-red)" points="0,193 995,193 1300,55 1420,145 1420,212 1300,125 800,460 0,460"/>
    </svg>
    <div class="bottom-rule"></div>
    <div class="ceo-photo" role="img" aria-label="Photo of the company CEO in a light denim shirt, smiling and pointing up at the headline"></div>

    <h1 class="headline">SELLING YOUR HOME?</h1>
    <p class="offer-kicker">GET A CASH OFFER</p>
    <p class="offer-main">SAME DAY</p>

    <p class="phone">865-555-0142</p>
    <div class="divider"></div>
    <p class="company-name">BRIGHT LANE<br>PROPERTY GROUP</p>
    <p class="website">www.brightlanepropertygroup.com</p>
  </section>
</body>
</html>
```